Home Security Company Business Card

Looking for a eye catching business card that is non traditional and stands out but yet still looks professional. It should include all the pertinent information such as name, title, address, telephone, e-mail, website address should definitely stand out and then finally the logo.

Target Market(s)

Residential and Commercial accounts mostly upscale accounts

Industry/Entity Type

Security

Contact Information for Business Card

Name
Title
Address
Office #
Cell #
E-mail
Website

Font styles to use
Serif
Sans Serif

Requirements
Must have
• Logo, two sided color configuration
Nice to have
• You decide
Should not have
• There really aren't any.

```html
<!DOCTYPE html>
<html lang="en">
<head>
<meta charset="utf-8">
<title>Harborline Home Protection – Business Card</title>
<link href="https://fonts.googleapis.com/css2?family=Open+Sans:wght@400;600;700&display=swap" rel="stylesheet">
<style>
  :root {
    --maroon: #7f1006;
    --maroon-dark: #6a0c04;
    --maroon-light: #a8392a;
    --gold: #f3c448;
    --gold-deep: #c9952e;
    --cream: #f7ecd0;
    --white: #ffffff;
    --backdrop: #ecebe8;
  }
  * { margin: 0; padding: 0; box-sizing: border-box; }
  html, body {
    width: 1200px; height: 900px; overflow: hidden;
    background: var(--backdrop);
    font-family: "Open Sans", Arial, sans-serif;
  }
  .canvas { position: relative; width: 1200px; height: 900px; }

  .card { position: absolute; width: 556px; height: 345px; overflow: hidden;
          box-shadow: 0 6px 18px rgba(0,0,0,.18); }

  /* Front side */
  .card-front { left: 238px; top: 60px; background: var(--maroon); }
  .front-top { position: absolute; left: 0; top: 0; width: 100%; height: 196px; background: var(--white); }
  .front-glow {
    position: absolute; right: 0; top: 0; width: 170px; height: 196px;
    background: linear-gradient(90deg, rgba(247,236,208,0) 0%, var(--cream) 35%, #e9cfc7 100%);
  }
  .gold-rule { position: absolute; left: 0; top: 196px; width: 100%; height: 7px;
               background: linear-gradient(90deg, var(--gold-deep), var(--gold), var(--gold-deep)); }
  .gold-pointer { position: absolute; left: 70px; top: 203px; }
  .front-brand {
    position: absolute; left: 150px; top: 76px; width: 260px;
    display: flex; align-items: center; gap: 10px;
    color: var(--maroon); font-weight: 700; font-size: 17px; line-height: 1.15; letter-spacing: .5px;
  }
  .brand-dot { flex: none; width: 30px; height: 30px; border-radius: 50%; background: var(--gold-deep); }

  .person { position: absolute; left: 39px; top: 236px; }
  .person-name { color: var(--gold); font-weight: 700; font-size: 18px; letter-spacing: .3px; }
  .person-title { color: var(--white); font-size: 14px; margin-top: 4px; }

  .contact-list { position: absolute; left: 262px; top: 236px; list-style: none; }
  .contact-list li { display: flex; align-items: center; gap: 8px; color: var(--white);
                     font-size: 14px; line-height: 20px; }
  .contact-list svg { width: 10px; height: 10px; fill: var(--gold); }

  /* Back side */
  .card-back { left: 457px; top: 518px; width: 560px; height: 344px;
               background: radial-gradient(ellipse at 52% 40%, var(--maroon-light) 0%, var(--maroon) 55%, var(--maroon-dark) 100%); }
  .back-brand {
    position: absolute; left: 0; top: 118px; width: 100%;
    display: flex; align-items: center; justify-content: center; gap: 14px;
    color: var(--white); font-weight: 700; font-size: 26px; line-height: 1.15; letter-spacing: 1px;
  }
  .back-brand .brand-dot { width: 44px; height: 44px; background: var(--gold); }
  .back-address { position: absolute; left: 0; bottom: 26px; width: 100%; text-align: center;
                  color: var(--white); font-size: 15px; }
</style>
</head>
<body>
<main class="canvas">

  <section class="card card-front" aria-label="Business card front">
    <div class="front-top"></div>
    <div class="front-glow"></div>
    <div class="gold-rule"></div>
    <svg class="gold-pointer" width="24" height="12" viewBox="0 0 24 12" aria-hidden="true">
      <polygon points="0,0 24,0 12,12" fill="#c9952e"/>
    </svg>
    <div class="front-brand">
      <span class="brand-dot"></span>
      <span class="brand-name">HARBORLINE<br>HOME PROTECTION</span>
    </div>

    <div class="person">
      <p class="person-name">DANIEL HARTLEY</p>
      <p class="person-title">Managing Director</p>
    </div>

    <ul class="contact-list">
      <li><svg viewBox="0 0 10 10"><path d="M1 3 Q5 0 9 3 L8 5 L6.5 4 L6.5 3.2 Q5 2.7 3.5 3.2 L3.5 4 L2 5 Z M2 6 H8 V9 H2 Z"/></svg>044-555 018 234</li>
      <li><svg viewBox="0 0 10 10"><path d="M3 0 H7 Q8 0 8 1 V9 Q8 10 7 10 H3 Q2 10 2 9 V1 Q2 0 3 0 Z M3 1.5 V7.5 H7 V1.5 Z"/></svg>044-555 018 235</li>
      <li><svg viewBox="0 0 10 10"><path d="M0 2 H10 V8 H0 Z M0.5 2.3 L5 5.5 L9.5 2.3" stroke="#7f1006" stroke-width=".8"/></svg>INFO@HARBORLINEHOME.COM</li>
      <li><svg viewBox="0 0 10 10"><path d="M1 7 L3 9 L6 6 L5 5 L3 7 L3 7 Z M4 4 L7 1 L9 3 L6 6 L5 5 L7 3 L7 3 Z"/></svg>WWW.HARBORLINEHOME.COM</li>
    </ul>
  </section>

  <section class="card card-back" aria-label="Business card back">
    <div class="back-brand">
      <span class="brand-dot"></span>
      <span class="brand-name">HARBORLINE<br>HOME PROTECTION</span>
    </div>
    <p class="back-address">12345, Address Goes Here Country Name, 123456.</p>
  </section>

</main>
</body>
</html>
```